New Webpage for High Class Expert Witness Services Company

We are looking for a minimalist design for a webpage that just has our logo and an entry form offer to connect with one of our Liaisons.
The entry form should just ask for Name, Email, Contact Info and Description of Project.

Company Name is: The Marlowe Crest Advisory Services

Number of Pages Required

1 page

```html
<!DOCTYPE html>
<html lang="en">
<head>
<meta charset="UTF-8">
<title>The Marlowe Crest Advisory Services</title>
<link href="https://fonts.googleapis.com/css2?family=Cardo:wght@400&display=swap" rel="stylesheet">
<style>
  :root {
    --white: #ffffff;
    --ink: #141414;
    --panel: #e8e8ea;
    --field-border: #a9a9ad;
    --placeholder: #8b8b8f;
    --hero-top: #a4a6a9;
    --hero-mid: #6f7480;
    --hero-bottom: #262d3b;
  }
  * { box-sizing: border-box; margin: 0; padding: 0; }
  html, body { width: 1200px; height: 675px; overflow: hidden; background: var(--white); }
  body { font-family: "Cardo", Georgia, serif; position: relative; }

  .site-header {
    position: absolute; left: 0; top: 0; width: 1200px; height: 78px;
    background: var(--white);
    display: flex; align-items: center; justify-content: center; gap: 10px;
  }
  .brand-mark { width: 14px; height: 14px; background: var(--ink); }
  .brand-name { font-size: 22px; color: var(--ink); letter-spacing: 0.5px; white-space: nowrap; }

  .hero {
    position: absolute; left: 0; top: 78px; width: 1200px; height: 597px;
  }
  .hero-photo {
    position: absolute; inset: 0;
    background: linear-gradient(180deg, var(--hero-top) 0%, var(--hero-mid) 55%, var(--hero-bottom) 100%);
  }
  .hero-title {
    position: absolute; left: 0; width: 1200px; top: 438px;
    text-align: center; color: var(--white); white-space: nowrap;
    font-size: 41px; font-weight: 400; line-height: 1; letter-spacing: 0.2px;
  }

  .contact-form {
    position: absolute; left: 91px; top: 507px; width: 1018px; height: 71px;
    background: var(--panel);
    display: flex; align-items: center; padding: 0 19px; gap: 7px;
  }
  .contact-form input {
    width: 203px; height: 34px; border: 1px solid var(--field-border);
    background: var(--white); font-family: "Cardo", Georgia, serif;
    font-size: 14px; padding: 0 9px; color: var(--ink);
  }
  .contact-form input::placeholder { color: var(--placeholder); }
  .submit-button {
    margin-left: 6px; width: 137px; height: 34px; border: none;
    background: var(--ink); color: var(--white);
    font-family: "Cardo", Georgia, serif; font-size: 15px; letter-spacing: 0.3px;
  }
</style>
</head>
<body>
  <header class="site-header">
    <span class="brand-mark"></span>
    <span class="brand-name">The Marlowe Crest Advisory Services</span>
  </header>

  <section class="hero">
    <div class="hero-photo" role="img" aria-label="Five smiling business professionals in suits seated around a glass conference table in a bright office"></div>
    <h1 class="hero-title">FOCUSED PROTECTION. TRUSTED EXPERTISE.</h1>
    <form class="contact-form">
      <input type="text" placeholder="Name">
      <input type="email" placeholder="Email">
      <input type="text" placeholder="Contact Info">
      <input type="text" placeholder="Description of Project">
      <button type="button" class="submit-button">SUBMIT</button>
    </form>
  </section>
</body>
</html>
```